Design a website for our small self storage business

We're looking for a freelance web designer who can produce a good-looking design for our small business website (no coding necessary). We will provide a list of pages to design, along with content outlines.

Key skills:
- Graphic design
- Responsive web design
- Proficiency with a modern web design tool such as Figma, Adobe Xd, or InVision

Please send relevant previous work (preferably in an inspectable format such as Figma or Invision).

```html
<!DOCTYPE html>
<html lang="en">
<head>
<meta charset="utf-8">
<title>Baywell Self Storage – Elm Park</title>
<link rel="stylesheet" href="https://fonts.googleapis.com/css2?family=Montserrat:wght@600;700;800&family=Roboto:wght@400;500;700&display=swap">
<style>
:root{
  --navy:#0b4a8c;
  --navy-dark:#083a70;
  --red:#e3191f;
  --sky:#e7f2fc;
  --ink:#1d1d1d;
  --body:#555;
  --white:#fff;
  --black:#000;
  --faq-plus:#3a8fe0;
}
*{box-sizing:border-box;margin:0;padding:0}
html,body{width:1200px;height:3542px;overflow:hidden;background:var(--white)}
body{font-family:"Roboto",Arial,sans-serif;color:var(--body);position:relative}
.abs{position:absolute}
.heading{font-family:"Montserrat",Arial,sans-serif;font-weight:800;letter-spacing:.3px}
.btn{position:absolute;display:flex;align-items:center;justify-content:center;gap:8px;font-family:"Roboto",Arial,sans-serif;font-weight:700;font-size:14px;color:var(--white);background:var(--red);border-radius:3px;text-transform:uppercase}
.btn .dot{width:13px;height:13px;border-radius:50%;background:var(--white);display:inline-block;position:relative}
.btn .dot::after{content:"";position:absolute;left:4px;top:3.5px;border-left:5px solid var(--red);border-top:3px solid transparent;border-bottom:3px solid transparent}
.btn.blue{background:var(--navy)}
.btn.blue .dot::after{border-left-color:var(--navy)}

/* header */
.topbar{left:440px;top:0;width:760px;height:44px;background:var(--navy);clip-path:polygon(0 0,100% 0,100% 100%,45px 100%)}
.topbar-item{top:10px;display:flex;align-items:center;gap:14px;color:var(--white);font-size:15px}
.topbar-item .ic{width:28px;height:28px;border-radius:50%;background:var(--red);display:flex;align-items:center;justify-content:center}
.phone-top{font-weight:700;font-size:18px}
.logo{left:110px;top:14px;display:flex;align-items:center;gap:10px}
.logo-mark{width:34px;height:34px;background:var(--red)}
.logo-name{font-family:"Montserrat",Arial,sans-serif;font-weight:700;color:var(--navy);font-size:22px;line-height:1.05}
.nav a{position:absolute;top:71px;font-family:"Roboto",Arial,sans-serif;font-size:14.5px;font-weight:500;color:var(--ink);text-decoration:none}
.nav a.active{color:var(--red)}
.nav a.active::after{content:"";position:absolute;left:0;right:0;bottom:-6px;height:2px;background:var(--red)}

/* hero */
.hero-photo{left:0;top:118px;width:1200px;height:625px;background:linear-gradient(90deg,#1f5d9a 0%,#3f5f80 18%,#6f7378 40%,#7d7d7d 50%,#6f7378 60%,#3f5f80 82%,#1f5d9a 100%)}
.hero-shade{left:0;top:118px;width:1200px;height:625px;background:rgba(10,20,35,.35)}
.hero-text{left:0;width:1200px;text-align:center;color:var(--white)}
.arrow-btn{width:36px;height:36px;border-radius:50%;background:var(--white);display:flex;align-items:center;justify-content:center;top:334px}

/* advantages */
.adv-bg{left:0;top:700px;width:1200px;height:576px;background:var(--sky)}
.section-title{font-family:"Montserrat",Arial,sans-serif;font-weight:800;color:var(--navy);font-size:31px}
.section-title span{color:var(--red)}
.rule{height:3px;background:var(--navy)}
.card{top:846px;width:311px;height:330px;background:var(--white);border-radius:12px;box-shadow:0 4px 16px rgba(11,74,140,.08);text-align:center}
.card .icon{width:104px;height:104px;border-radius:50%;background:var(--navy);margin:20px auto 0;display:flex;align-items:center;justify-content:center}
.card h3{font-family:"Montserrat",Arial,sans-serif;font-weight:700;font-size:19px;color:var(--navy);margin-top:25px}
.card .line{width:34px;height:2px;background:var(--navy);margin:13px auto 0}
.card p{font-size:14px;line-height:22px;margin:17px 24px 0}
.card .go{width:18px;height:18px;border-radius:50%;background:var(--navy);margin:14px auto 0;position:relative}
.card .go::after{content:"";position:absolute;left:7px;top:5px;border-left:5px solid var(--white);border-top:4px solid transparent;border-bottom:4px solid transparent}
.card.featured{background:var(--red);box-shadow:0 8px 22px rgba(227,25,31,.35)}
.card.featured .icon{background:var(--white)}
.card.featured h3,.card.featured p{color:var(--white)}
.card.featured .line,.card.featured .go{background:var(--white)}
.card.featured .go::after{border-left-color:var(--red)}

/* about */
.about-text{left:643px;top:1461px;width:445px;font-size:14.5px;line-height:24px;text-align:justify;color:var(--body)}
.about-text b{color:var(--red);font-weight:500}
.about-text em{font-style:normal;color:var(--red)}

/* split panels */
.panel{color:var(--white);text-align:center}
.panel h2{font-family:"Montserrat",Arial,sans-serif;font-weight:800;font-size:22px}
.panel .rule{background:var(--white);width:36px;margin:14px auto 0}
.panel p{font-size:14.5px;line-height:25px;text-align:justify;margin-top:20px}

/* faq */
.faq{left:609px;width:521px;height:61px;background:var(--navy);display:flex;align-items:center}
.faq .plus{width:62px;height:100%;background:var(--faq-plus);color:var(--white);font-size:28px;font-weight:700;display:flex;align-items:center;justify-content:center}
.faq .q{color:var(--white);font-weight:700;font-size:13.5px;margin-left:38px}

/* footer */
.footer-h{font-family:"Roboto",Arial,sans-serif;font-weight:700;color:var(--white);font-size:13.5px;text-transform:uppercase}
.field{position:absolute;background:var(--white);font-size:14px;color:#777;padding:13px 8px}
.foot-txt{color:var(--white);font-size:14px;line-height:25px}
.foot-ic{width:30px;height:30px;border-radius:50%;background:var(--white);display:flex;align-items:center;justify-content:center}
.links li{list-style:none;color:var(--white);font-size:14px;height:34.5px}
.links li::before{content:"»";margin-right:12px}
.social{width:28px;height:28px;border-radius:50%;top:3375px}
</style>
</head>
<body>

<!-- header -->
<div class="abs topbar"></div>
<div class="abs topbar-item" style="left:576px">
  <span class="ic"><svg width="14" height="10" viewBox="0 0 14 10"><rect x="0.5" y="0.5" width="13" height="9" fill="none" stroke="#fff"/><path d="M1 1l6 5 6-5" fill="none" stroke="#fff"/></svg></span>
  <span>info@baywellselfstorage.com</span>
</div>
<div class="abs" style="left:844px;top:8px;color:#fff;font-size:18px">|</div>
<div class="abs topbar-item" style="left:894px;top:8px">
  <span class="ic"><svg width="13" height="13" viewBox="0 0 24 24"><path fill="#fff" d="M6.6 10.8a15.1 15.1 0 006.6 6.6l2.2-2.2c.3-.3.7-.4 1-.2 1.1.4 2.3.6 3.6.6.6 0 1 .4 1 1V20c0 .6-.4 1-1 1A17 17 0 013 4c0-.6.4-1 1-1h3.5c.6 0 1 .4 1 1 0 1.3.2 2.5.6 3.6.1.3 0 .7-.2 1z"/></svg></span>
  <span class="phone-top">+ 1 888 888 8888</span>
</div>

<div class="abs logo">
  <span class="logo-mark"></span>
  <span class="logo-name">BAYWELL<br>SELF STORAGE<br>ELM PARK</span>
</div>

<nav class="nav">
  <a class="active" style="left:468px">Home</a>
  <a style="left:554px">About</a>
  <a style="left:641px">Units</a>
  <a style="left:722px">Pay Online</a>
  <a style="left:839px">Contact</a>
</nav>
<div class="btn" style="left:949px;top:60px;width:139px;height:40px;font-size:13.5px">Get Started <span class="dot"></span></div>

<!-- hero -->
<div class="abs hero-photo" role="img" aria-label="Photo of an indoor storage corridor lined with blue roll-up unit doors"></div>
<div class="abs hero-shade"></div>
<div class="abs hero-text heading" style="top:256px;font-size:27px;font-weight:700">WELCOME TO</div>
<div class="abs hero-text heading" style="top:298px;font-size:60px;line-height:64px">BAYWELL SELF<br>STORAGE</div>
<div class="abs hero-text" style="top:438px;font-size:17px;line-height:26px">Sed ut perspiciatis unde omnis iste natus error sit voluptatem<br>accusantium doloremque laudantium</div>
<div class="btn" style="left:531px;top:520px;width:139px;height:40px">Get Started <span class="dot"></span></div>
<div class="abs arrow-btn" style="left:36px"><svg width="12" height="14" viewBox="0 0 12 14"><path d="M8 2L3 7l5 5" fill="none" stroke="#111" stroke-width="2"/></svg></div>
<div class="abs arrow-btn" style="left:1128px"><svg width="12" height="14" viewBox="0 0 12 14"><path d="M4 2l5 5-5 5" fill="none" stroke="#111" stroke-width="2"/></svg></div>

<svg class="abs" style="left:0;top:580px" width="1200" height="170" viewBox="0 0 1200 170">
  <polygon points="0,140 337,28 1200,150 1200,170 0,170" fill="#0b4a8c"/>
  <polygon points="0,163 337,50 1200,163 1200,170 0,170" fill="#e7f2fc"/>
</svg>

<!-- advantages -->
<div class="abs adv-bg" style="top:743px;height:533px"></div>
<div class="abs section-title" style="left:0;width:1200px;text-align:center;top:750px">KEY <span>ADVANTAGES</span></div>
<div class="abs rule" style="left:582px;top:800px;width:36px"></div>

<div class="abs card" style="left:100px">
  <div class="icon"><svg width="54" height="54" viewBox="0 0 54 54"><circle cx="30" cy="16" r="11" fill="none" stroke="#fff" stroke-width="3"/><path d="M30 10v12M27 13h5a2 2 0 010 4h-4a2 2 0 000 4h5" fill="none" stroke="#fff" stroke-width="2"/><path d="M6 36h10l10 4h10l10-8v6L34 48H8z" fill="#fff"/></svg></div>
  <h3>Affordable</h3><div class="line"></div>
  <p>Sed ut perspiciatis unde omnis iste natus error sit voluptatem accusant doloremque laudantium, totam rem aperiam</p>
  <div class="go"></div>
</div>
<div class="abs card featured" style="left:445px">
  <div class="icon"><svg width="54" height="54" viewBox="0 0 54 54"><path d="M27 5l18 7v12c0 12-8 21-18 25C17 45 9 36 9 24V12z" fill="#e3191f"/><circle cx="27" cy="27" r="10" fill="none" stroke="#fff" stroke-width="3"/><path d="M22 27l4 4 6-7" fill="none" stroke="#fff" stroke-width="3"/></svg></div>
  <h3>Secure</h3><div class="line"></div>
  <p>Sed ut perspiciatis unde omnis iste natus error sit voluptatem accusant doloremque laudantium, totam rem aperiam</p>
  <div class="go"></div>
</div>
<div class="abs card" style="left:789px">
  <div class="icon"><svg width="54" height="54" viewBox="0 0 54 54"><circle cx="27" cy="30" r="15" fill="none" stroke="#fff" stroke-width="5"/><rect x="22" y="6" width="10" height="5" fill="#fff"/><path d="M27 30V20" stroke="#fff" stroke-width="4"/></svg></div>
  <h3>Convenient</h3><div class="line"></div>
  <p>Sed ut perspiciatis unde omnis iste natus error sit voluptatem accusant doloremque laudantium, totam rem aperiam</p>
  <div class="go"></div>
</div>

<!-- about -->
<div class="abs" style="left:111px;top:1361px;width:153px;height:141px;background:var(--red)"></div>
<div class="abs" style="left:128px;top:1379px;width:334px;height:308px;background:var(--white);border-radius:8px;box-shadow:0 3px 12px rgba(0,0,0,.18);padding:6px">
  <div role="img" aria-label="Photo of outdoor storage units with red roll-up doors under a blue sky" style="width:100%;height:100%;border-radius:6px;background:linear-gradient(180deg,#7fb0e0 0%,#b24a64 25%,#8c1f3c 70%,#6c6c6c 100%)"></div>
</div>
<div class="abs" style="left:349px;top:1526px;width:218px;height:202px;background:var(--white);border-radius:8px;box-shadow:0 3px 12px rgba(0,0,0,.18);padding:5px">
  <div role="img" aria-label="Photo of a row of storage units with orange doors" style="width:100%;height:100%;border-radius:6px;background:linear-gradient(180deg,#c9cccf 0%,#d96330 35%,#b94b22 65%,#8b8b8b 100%)"></div>
</div>
<div class="abs section-title" style="left:643px;top:1382px;font-size:33px">ABOUT <span>US</span></div>
<div class="abs about-text">
  <b>Baywell Self Storage Elm Park</b> Located on Marlow St. between Fenwick Ave. and Castor Ave. near Elm Park City Hall in Cedar Ridge Valley.<br>
  For most people, finding self storage is a matter of locating the intersection of <em>convenience, security, quality, and price</em>. This isn't such a simple equation. On our website you can find our self storage price quickly and easily. We've got a great selection of storage units of various sizes in the heart of Cedar Ridge Valley - downtown area Elm Park.
</div>
<div class="btn" style="left:643px;top:1695px;width:138px;height:42px;font-size:13.5px">Learn More <span class="dot"></span></div>

<!-- split panels -->
<div class="abs panel" style="left:0;top:1836px;width:600px;height:514px;background:var(--navy);padding:76px 77px 0">
  <h2>DRIVE-UP SPACES</h2><div class="rule"></div>
  <p>Lorem ipsum dolor sit amet, consectetur adipiscing elit, sed do eiusmod tempor incididunt ut labore et dolore magna aliqua. Ut enim ad minim veniam, quis nostrud exercitation ullamco laboris nisi ut aliquip ex ea commodo consequat. Duis aute irure dolor in reprehenderit in voluptate velit esse cillum dolore eu fugiat nulla pariatur. Excepteur sint occaecat cupidatat non proident, sunt in culpa qui officia deserunt mollit anim id est laborum Lorem ipsum dolor sit amet, consectetur adipiscing elit, sed do eiusmod tempor incididunt ut labore et dolore magna aliqua.</p>
</div>
<div class="btn" style="left:231px;top:2234px;width:136px;height:42px;font-size:13.5px">Learn More <span class="dot"></span></div>

<div class="abs panel" style="left:600px;top:1878px;width:600px;height:514px;background:var(--red);padding:76px 77px 0">
  <h2>JUST SHOW UP WITH YOUR STUFF</h2><div class="rule"></div>
  <p>Lorem ipsum dolor sit amet, consectetur adipiscing elit, sed do eiusmod tempor incididunt ut labore et dolore magna aliqua. Ut enim ad minim veniam, quis nostrud exercitation ullamco laboris nisi ut aliquip ex ea commodo consequat. Duis aute irure dolor in reprehenderit in voluptate velit esse cillum dolore eu fugiat nulla pariatur. Excepteur sint occaecat cupidatat non proident, sunt in culpa qui officia deserunt mollit anim id est laborum Lorem ipsum dolor sit amet, consectetur adipiscing elit, sed do eiusmod tempor incididunt ut labore et dolore magna aliqua.</p>
</div>
<div class="btn blue" style="left:832px;top:2277px;width:136px;height:42px;font-size:13.5px">Learn More <span class="dot"></span></div>

<!-- footer base -->
<div class="abs" style="left:0;top:3000px;width:1200px;height:542px;background:var(--black)"></div>

<!-- faq -->
<div class="abs" style="left:0;top:2483px;width:528px;height:583px;border-top:8px solid var(--red);border-right:8px solid var(--red)">
  <div role="img" aria-label="Photo of a paved lane between two long rows of storage buildings under a cloudy sky" style="width:100%;height:100%;background:linear-gradient(180deg,#8fa6bf 0%,#d7dde3 35%,#6a7a5a 55%,#4a4a4a 75%,#2f2f33 100%)"></div>
</div>
<svg class="abs" style="left:0;top:2990px" width="1200" height="160" viewBox="0 0 1200 160">
  <polygon points="528,0 1200,0 1200,12 900,120 528,83" fill="#fff"/>
  <polygon points="0,68 528,83 900,120 1200,12 1200,40 900,150 0,95" fill="#0b4a8c"/>
</svg>

<div class="abs section-title" style="left:608px;top:2482px;font-size:32px">FREQUENTLY ASKED <span>QUESTIONS</span></div>
<div class="abs rule" style="left:609px;top:2531px;width:36px"></div>

<div class="abs" style="left:609px;top:2581px;width:521px;height:176px;background:var(--white);box-shadow:0 3px 12px rgba(0,0,0,.15)">
  <div class="faq" style="left:0;top:0;position:absolute"><span class="plus">–</span><span class="q">NEMO ENIM IPSAM VOLUPTATEM QUIA VOLUPTAS ?</span></div>
  <div class="abs" role="img" aria-label="Small photo of an indoor storage hallway" style="left:14px;top:74px;width:106px;height:86px;background:linear-gradient(90deg,#5b6c80,#c9ced4,#5b6c80)"></div>
  <div class="abs" style="left:143px;top:80px;width:365px;font-size:14px;line-height:22px;color:var(--body)">Sed ut perspiciatis unde omnis iste natuerrovoluptatem accusantium doloremque laudantium.totam reaperiam, eaque ipsa quae ab illo inventore</div>
</div>
<div class="faq abs" style="top:2775px"><span class="plus">+</span><span class="q">NEMO ENIM IPSAM VOLUPTATEM QUIA VOLUPTAS ?</span></div>
<div class="faq abs" style="top:2850px"><span class="plus">+</span><span class="q">NEMO ENIM IPSAM VOLUPTATEM QUIA VOLUPTAS ?</span></div>
<div class="faq abs" style="top:2926px"><span class="plus">+</span><span class="q">NEMO ENIM IPSAM VOLUPTATEM QUIA VOLUPTAS ?</span></div>

<!-- footer -->
<div class="abs footer-h" style="left:111px;top:3170px;font-size:16px">Get in touch</div>
<div class="field" style="left:111px;top:3211px;width:223px;height:43px">First Name</div>
<div class="field" style="left:344px;top:3211px;width:223px;height:43px">Last Name</div>
<div class="field" style="left:111px;top:3263px;width:223px;height:43px">Email</div>
<div class="field" style="left:344px;top:3263px;width:223px;height:43px">Phone No</div>
<div class="field" style="left:111px;top:3314px;width:456px;height:78px">Message</div>
<div class="btn" style="left:111px;top:3403px;width:117px;height:42px;border-radius:21px;font-size:16px">Submit</div>

<div class="abs footer-h" style="left:628px;top:3172px">Contact info</div>
<div class="abs foot-ic" style="left:628px;top:3210px"><svg width="12" height="16" viewBox="0 0 12 16"><path d="M6 0a6 6 0 016 6c0 4-6 10-6 10S0 10 0 6a6 6 0 016-6z" fill="#e3191f"/><circle cx="6" cy="6" r="2.2" fill="#fff"/></svg></div>
<div class="abs foot-txt" style="left:674px;top:3200px">145 , Lorem Ipsum Dolor<br>United States</div>
<div class="abs foot-ic" style="left:628px;top:3265px"><svg width="14" height="14" viewBox="0 0 24 24"><path fill="#e3191f" d="M6.6 10.8a15.1 15.1 0 006.6 6.6l2.2-2.2c.3-.3.7-.4 1-.2 1.1.4 2.3.6 3.6.6.6 0 1 .4 1 1V20c0 .6-.4 1-1 1A17 17 0 013 4c0-.6.4-1 1-1h3.5c.6 0 1 .4 1 1 0 1.3.2 2.5.6 3.6.1.3 0 .7-.2 1z"/></svg></div>
<div class="abs foot-txt" style="left:674px;top:3266px;font-weight:700;font-size:17px">+1 888 888 8888</div>
<div class="abs foot-ic" style="left:628px;top:3317px"><svg width="16" height="16" viewBox="0 0 16 16"><circle cx="8" cy="8" r="6.5" fill="none" stroke="#e3191f" stroke-width="1.6"/><path d="M8 4v4h3" fill="none" stroke="#e3191f" stroke-width="1.6"/></svg></div>
<div class="abs foot-txt" style="left:674px;top:3320px">Sun - Sat : 09.30 - 05.30</div>

<div class="abs footer-h" style="left:953px;top:3172px">Quick links</div>
<ul class="abs links" style="left:953px;top:3200px">
  <li>Home</li><li>About Us</li><li>Pay Online</li><li>Contact Us</li><li>Units</li>
</ul>

<div class="abs footer-h" style="left:628px;top:3380px;font-size:16px;text-transform:uppercase">Stay connected</div>
<div class="abs social" style="left:804px;background:#3b5998" aria-label="Social profile"></div>
<div class="abs social" style="left:842px;background:#1da1f2" aria-label="Social profile"></div>
<div class="abs social" style="left:880px;background:#dd4b39" aria-label="Social profile"></div>
<div class="abs social" style="left:918px;background:#0077b5" aria-label="Social profile"></div>
<div class="abs social" style="left:956px;background:#e3191f" aria-label="Social profile"></div>

<div class="abs" style="left:111px;top:3469px;width:977px;height:1px;background:#333"></div>
<div class="abs foot-txt" style="left:111px;top:3489px">© 2022 Baywell Self Storage. All Rights reserved</div>
<div class="abs" style="left:947px;top:3481px;width:139px;height:42px;background:var(--white);border-radius:4px" aria-label="Accepted payment methods"></div>

</body>
</html>
```